Informational Site for Advanced Chemistry R&D

The company develops oxidation chemistry for air, water, fuel pollution controls. The site has been prototyped at www.velquaresearch.example. Take a look. Now, the task is to design it for eye-catching beauty with use of color, on-page scroll-driven color transition and parallax effects. Should capture the themes: high technology, wow it's beautiful, modern, uncluttered, clean urban environment.

Target Market(s)

China Environmentally Conscious Government and Industry,

Industry/Entity Type

It Company

Number of Pages Required

3 page

Font styles to use
Sans Serif

Requirements
Must have
• Parallax effects, desktop compatible, Rich, Modern, Simple, Graphic
Nice to have
• Mobile Phone Compatible
Should not have
• Flash, or anything that is slow to load or requires high bandwidth

```html
<!DOCTYPE html>
<html lang="en">
<head>
<meta charset="utf-8">
<title>Velquara — Advanced Oxidation Science</title>
<link href="https://fonts.googleapis.com/css2?family=Questrial&family=Open+Sans:wght@400;600&display=swap" rel="stylesheet">
<style>
:root{
  --page:#f0f1f1;
  --brand:#1f6fb4;
  --teal:#2bbfb4;
  --teal-dark:#1f9fa0;
  --ink:#555b60;
  --ink-soft:#7a8086;
  --dark:#0d1116;
  --footer:#2e3134;
  --field:#3a3d41;
  --white:#ffffff;
}
*{margin:0;padding:0;box-sizing:border-box}
html,body{width:1200px;height:3098px;overflow:hidden;background:var(--page)}
body{font-family:"Open Sans",Arial,sans-serif;color:var(--ink)}
.canvas{position:relative;width:1200px;height:3098px;overflow:hidden}
.backdrop{position:absolute;left:0;top:0}
.abs{position:absolute}
h1,h2,h3,.nav a,.brand{font-family:"Questrial","Helvetica Neue",sans-serif;font-weight:400}

/* header */
.site-header{position:absolute;left:0;top:0;width:1200px;height:108px;background:var(--white);border-bottom:3px solid var(--teal)}
.brand{position:absolute;left:99px;top:38px;display:flex;align-items:center;gap:10px;font-size:28px;color:var(--brand)}
.brand-dot{width:26px;height:26px;border-radius:50%;background:var(--teal)}
.nav{position:absolute;right:72px;top:50px;display:flex;gap:70px}
.nav a{font-size:13px;color:#777;text-decoration:none;letter-spacing:.5px;position:relative}
.nav a.active{color:var(--brand)}
.nav a.active::before{content:"";position:absolute;left:50%;top:-16px;width:44px;height:44px;margin-left:-22px;border:1px solid #dfe3e6;border-radius:50%}
.nav a.active::after{content:"";position:absolute;left:50%;bottom:-30px;margin-left:-7px;border:7px solid transparent;border-bottom-color:var(--teal)}

/* hero */
.hero-title{left:0;top:310px;width:1200px;text-align:center;color:var(--white);font-size:42px;line-height:60px}
.hero-dots{left:556px;top:600px;display:flex;gap:14px}
.hero-dots span{width:9px;height:9px;border-radius:50%;background:rgba(255,255,255,.55)}
.hero-dots span.on{background:var(--white)}

/* welcome */
.section-title{left:0;width:1200px;text-align:center;font-size:29px;letter-spacing:.5px}
.welcome-title{top:770px;color:var(--brand)}
.welcome-text{left:170px;top:822px;width:860px;text-align:center;font-size:13.5px;line-height:22px;color:var(--ink-soft)}
.feature{top:902px;width:320px;height:110px}
.feature-icon{position:absolute;left:0;top:5px;width:92px;height:92px;border:2px solid #cdd7dc;border-radius:50%;display:flex;align-items:center;justify-content:center}
.feature-icon i{width:58px;height:58px;border-radius:50%;background:var(--teal);display:flex;align-items:center;justify-content:center}
.feature h3{position:absolute;left:100px;top:0;font-size:20px;color:var(--teal)}
.feature p{position:absolute;left:100px;top:34px;width:210px;font-size:11.5px;line-height:20px;color:var(--ink-soft)}

/* oxidation */
.dark-title{top:1182px;color:var(--white)}
.dark-text{left:200px;top:1238px;width:800px;text-align:center;color:#e8ecef;font-size:16px;line-height:28px}
.bullets{left:230px;top:1320px;width:760px;display:flex;justify-content:space-between;color:#e8ecef;font-size:15px}
.bullets li{list-style:none;padding-left:34px;position:relative}
.bullets li::before{content:"";position:absolute;left:0;top:8px;width:8px;height:8px;border-radius:50%;background:var(--white)}
.dark-note{left:250px;top:1368px;width:700px;text-align:center;color:#d7dde2;font-size:13.5px;line-height:27px}

/* solutions */
.solutions-title{top:1596px;color:var(--white)}
.card{top:1673px;width:246px;height:355px;background:rgba(232,240,246,.93)}
.card-media{width:246px;height:182px}
.card h3{font-family:"Open Sans",Arial,sans-serif;font-weight:600;font-size:15px;color:#24303a;margin:20px 0 0 20px}
.card p{margin:12px 16px 0 20px;font-size:11.5px;line-height:20px;color:var(--ink-soft);text-align:justify}
.card .more{position:absolute;right:20px;bottom:22px;font-size:11.5px;color:var(--brand)}

/* partners */
.partners-title{top:2212px;color:var(--brand)}
.partner{top:2276px;width:241px;height:144px;background:#f6f7f7;border:1px solid #e3e6e7;text-align:center}
.partner-mark{height:92px;display:flex;align-items:center;justify-content:center}
.partner p{font-size:16px;color:#5e6469}
.partner-name{font-family:"Questrial",sans-serif;font-size:17px;color:var(--brand)}

/* contact */
.contact-title{top:2604px;color:var(--white)}
.address-label{left:98px;top:2693px;color:var(--white);font-size:13px;font-weight:600;letter-spacing:.5px;display:flex;align-items:center;gap:14px}
.address{left:127px;top:2742px;color:#d9dcde;font-size:14px;line-height:30px;font-style:italic}
.social{left:127px;top:2886px;display:flex;gap:34px}
.social span{width:14px;height:14px;border-radius:50%;background:#d9dcde}
.field{background:var(--field);color:#8e9397;font-size:13px;padding:0 18px;display:flex;align-items:center}
.field.focus{border-top:2px solid var(--teal);color:#e6e8ea}
.field.message{align-items:flex-start;padding-top:14px}
.send{left:950px;top:2990px;width:144px;height:46px;background:var(--teal);color:var(--white);font-size:15px;display:flex;align-items:center;justify-content:center;border-radius:2px}
.copyright{left:106px;top:3014px;font-size:12px;color:#d9dcde;letter-spacing:.3px}
.copyright b{font-weight:400;color:var(--teal)}
</style>
</head>
<body>
<div class="canvas">

<svg class="backdrop" width="1200" height="3098" viewBox="0 0 1200 3098">
  <defs>
    <linearGradient id="heroGrad" x1="0" y1="0" x2="1" y2="1">
      <stop offset="0" stop-color="#8cc4ec"/>
      <stop offset=".5" stop-color="#4e9ee0"/>
      <stop offset="1" stop-color="#1d70c8"/>
    </linearGradient>
    <linearGradient id="darkGrad" x1="0" y1="0" x2="1" y2="0">
      <stop offset="0" stop-color="#07090c"/>
      <stop offset=".5" stop-color="#1b2027"/>
      <stop offset="1" stop-color="#07090c"/>
    </linearGradient>
    <linearGradient id="blueGrad" x1="0" y1="0" x2="1" y2="1">
      <stop offset="0" stop-color="#1a5f92"/>
      <stop offset=".5" stop-color="#1f80bd"/>
      <stop offset="1" stop-color="#3a9ad6"/>
    </linearGradient>
  </defs>
  <path role="img" aria-label="Hero backdrop: blue molecular structures and water droplets" fill="url(#heroGrad)" d="M0 108H1200V560C1060 700 860 560 660 640C460 720 220 690 0 600Z"/>
  <path role="img" aria-label="Dark backdrop: astronaut floating in starry space" fill="url(#darkGrad)" d="M0 1040C300 1120 520 960 800 1020C1000 1060 1100 1000 1200 980V1520H0Z"/>
  <path role="img" aria-label="Blue backdrop with faint network lines" fill="url(#blueGrad)" d="M0 1540C250 1440 500 1520 750 1470C950 1430 1100 1400 1200 1420V2120C1000 2200 700 2120 450 2170C250 2210 100 2150 0 2120Z"/>
  <path fill="var(--footer)" d="M0 2560C200 2480 360 2530 600 2480C850 2430 1000 2520 1200 2460V3098H0Z"/>
</svg>

<header class="site-header">
  <div class="brand"><span class="brand-dot"></span>Velquara</div>
  <nav class="nav">
    <a class="active" href="#">HOME</a>
    <a href="#">TECHNOLOGY</a>
    <a href="#">PRODUCTS</a>
    <a href="#">CONTACT</a>
  </nav>
</header>

<h1 class="abs hero-title">Advanced Oxidation Science for<br>Environmental Pollution Management</h1>
<div class="abs hero-dots"><span></span><span class="on"></span><span></span></div>

<h2 class="abs section-title welcome-title">WELCOME TO VELQUARA SERVICE</h2>
<p class="abs welcome-text">But I must explain to you how all this mistaken idea of denouncing pleasure and praising pain was born and I will give you a complete account of the system, and expound the actual teachings of the great explorer of the truth, the master-builder of human .</p>

<div class="abs feature" style="left:99px">
  <div class="feature-icon"><i><svg width="22" height="28" viewBox="0 0 22 28"><path d="M11 1C11 1 2 13 2 18a9 9 0 0 0 18 0C20 13 11 1 11 1Z" fill="#fff"/></svg></i></div>
  <h3>WATER</h3>
  <p>Duis aute irure dolor in reprehenderit in voluptate velit esse cillum dolore eu fugiat nulla pariatur.</p>
</div>
<div class="abs feature" style="left:444px">
  <div class="feature-icon" style="border-color:#cdd7dc"><svg width="40" height="34" viewBox="0 0 40 34"><path d="M2 16L38 2L28 32L19 21Z M19 21L38 2" fill="none" stroke="var(--teal)" stroke-width="2.5" stroke-linejoin="round"/></svg></div>
  <h3>AIR</h3>
  <p>Duis aute irure dolor in reprehenderit in voluptate velit esse cillum dolore eu fugiat nulla pariatur.</p>
</div>
<div class="abs feature" style="left:791px">
  <div class="feature-icon"><i><svg width="30" height="20" viewBox="0 0 30 20"><text x="15" y="15" text-anchor="middle" font-family="Open Sans, sans-serif" font-size="14" fill="#fff">bio</text></svg></i></div>
  <h3>FUEL</h3>
  <p>Duis aute irure dolor in reprehenderit in voluptate velit esse cillum dolore eu fugiat nulla pariatur.</p>
</div>

<h2 class="abs section-title dark-title">ADVANCED OXIDATION</h2>
<p class="abs dark-text">Advanced Oxidation refers to a variety of techniques employing the Hydroxyl Radical,<br>an energetic, highly reactive cousin of the water molecule:</p>
<ul class="abs bullets">
  <li>To add oxygen to inorganic molecules</li>
  <li>To remove hydrogen from organic molecules</li>
</ul>
<p class="abs dark-note">These transformations convert important industrial contaminants into reactive forms<br>that can be captured or that disintegrate into harmless end products.</p>

<h2 class="abs section-title solutions-title">SOLUTIONS</h2>
<article class="abs card" style="left:99px">
  <div class="card-media" role="img" aria-label="Refinery towers and pipework in grey tones" style="background:linear-gradient(160deg,#c9cdd1,#5d646b)"></div>
  <h3>Fuel Oil Desulfurization</h3>
  <p>Our proprietary low temperature and pressure advanced oxidation catalytic process reliably removes sulfur from diesel transportation fuel at less</p>
  <span class="more">[ Learn More ]</span>
</article>
<article class="abs card" style="left:351px">
  <div class="card-media" role="img" aria-label="Worker handling blue chemical drums" style="background:linear-gradient(160deg,#6b86a4,#1d3f6c)"></div>
  <h3>Volatile Organic Compunds</h3>
  <p>Alkanes, alkenes, halogenated hydrocarbons, aromatic hydrocarbons, esters, aldehydes, polycyclic aromatic hydrocarbons.</p>
  <span class="more">[ Learn More ]</span>
</article>
<article class="abs card" style="left:603px">
  <div class="card-media" role="img" aria-label="Smokestacks releasing flue gas under a dusky sky" style="background:linear-gradient(180deg,#8e8ea8,#3a3a48)"></div>
  <h3>Flue Gas Scrubbing</h3>
  <p>Desulfurization and denitrification using our proprietary flue gas advanced oxidation catalytic process (FGAOC). Sulfur and nitrogen</p>
  <span class="more">[ Learn More ]</span>
</article>
<article class="abs card" style="left:857px">
  <div class="card-media" role="img" aria-label="Wastewater flowing from an outfall into a green river" style="background:linear-gradient(180deg,#5f7d4a,#9a8a66)"></div>
  <h3>Wastewater Treatment</h3>
  <p>Photoelectrocatalysed (PEC) anodic oxidation removes soluble organics. Novel anode design using our proprietary nano-carbon surface</p>
  <span class="more">[ Learn More ]</span>
</article>

<h2 class="abs section-title partners-title">PARTNERS</h2>
<div class="abs partner" style="left:99px">
  <div class="partner-mark"><span class="partner-name">Velquara Systems</span></div>
  <p>Our sales partner in China</p>
</div>
<div class="abs partner" style="left:353px">
  <div class="partner-mark"><svg width="48" height="48"><rect x="4" y="4" width="40" height="40" fill="#d8a23a"/></svg></div>
  <p>Our construction partner</p>
</div>
<div class="abs partner" style="left:607px">
  <div class="partner-mark"><svg width="80" height="80"><circle cx="40" cy="40" r="36" fill="#3a6aa3"/></svg></div>
  <p>Our technology partner</p>
</div>
<div class="abs partner" style="left:861px">
  <div class="partner-mark"><svg width="80" height="80"><circle cx="40" cy="40" r="36" fill="#b8303a"/></svg></div>
  <p>Our technology partner</p>
</div>

<h2 class="abs section-title contact-title">CONTACT US</h2>
<div class="abs address-label"><svg width="14" height="20" viewBox="0 0 14 20"><path d="M7 0A7 7 0 0 0 0 7C0 12 7 20 7 20S14 12 14 7A7 7 0 0 0 7 0Zm0 10a3 3 0 1 1 0-6 3 3 0 0 1 0 6Z" fill="var(--teal)"/></svg>ADDRESS</div>
<address class="abs address">410 Linden Row NW<br>Washington, DC 20001<br>(202) 555-0147<br>Mara Ellison</address>
<div class="abs social"><span></span><span></span><span></span><span></span></div>

<div class="abs field focus" style="left:450px;top:2691px;width:306px;height:42px">Ravi</div>
<div class="abs field" style="left:783px;top:2691px;width:307px;height:42px">Email</div>
<div class="abs field" style="left:450px;top:2761px;width:306px;height:42px">Telephone</div>
<div class="abs field" style="left:783px;top:2761px;width:307px;height:42px">Subject</div>
<div class="abs field message" style="left:450px;top:2829px;width:640px;height:131px">Message</div>
<div class="abs send">Send Now</div>

<p class="abs copyright">2016 ©<b>VELQUARA SERVICE</b>. ALL RIGHTS RESERVED.</p>

</div>
</body>
</html>
```